Business Cards Needed for Innovative Healthcare Marketing Company

We are a marketing company focused on healthcare. Our company is all about rebranding yourself renewing your image and generating results. The phoenix stands for "reborn" or "rising" which we provide new brands for our clients we take their old brands and renew it with creativity and innovation. I am looking for a business card with color dimension. I have attached an example of a card I think has the look and feel of what I am trying to accomplish. I like that the card example has black and grey font colors, I like the font placement and the small logo, I really like the use of the colors on the right those are the colors of my logo. My logo is phoenix so maybe incorporating flames similar to that design. I would like the back a solid color maybe red with an opaque version of the logo and website. As a marketing company I am always open to creative liberty!

Target Market(s)

Doctors and business professionals.

Industry/Entity Type

Marketing

Contact Information for Business Card

Valcorne Health Care Marketing
Marla Tenwick- CEO
#(512)638-2974
email-marla@valcorne.com
website- valcorne.com

Font styles to use
Sans Serif

Colors
ec1f27
f37122
ffc214
fbed22
fbf289
f04a50

Requirements
Must have
• The logo and required information
Nice to have
• icons by the information
Should not have
• child like font

```html
<!DOCTYPE html>
<html lang="en">
<head>
<meta charset="utf-8">
<title>Valcorne Health Care Marketing – Business Cards</title>
<link href="https://fonts.googleapis.com/css2?family=Josefin+Sans:wght@300;400&family=Open+Sans:wght@400;600&display=swap" rel="stylesheet">
<style>
  :root {
    --stage: #e9e6e3;
    --card-black: #080606;
    --white: #ffffff;
    --name-orange: #f7a21b;
    --title-red: #ec1f27;
    --rule-gold: #c9902a;
    --flame-deep: #7a1a14;
    --flame-mid: #b8401c;
    --flame-warm: #d98a1e;
    --back-orange: #ffa400;
    --back-yellow: #fff200;
    --brand-wine: #8e1c2c;
    --brand-ochre: #c0641e;
  }
  * { margin: 0; padding: 0; box-sizing: border-box; }
  html, body { width: 1200px; height: 900px; overflow: hidden; }
  body { background: var(--stage); position: relative; font-family: "Open Sans", sans-serif; }

  .card { position: absolute; overflow: hidden; }

  /* Front */
  .card-front { left: 78px; top: 35px; width: 587px; height: 362px; background: var(--card-black); }
  .front-art {
    position: absolute; left: 290px; top: 0; width: 297px; height: 362px;
    background:
      radial-gradient(ellipse 55% 48% at 55% 35%, rgba(184,64,28,.75), transparent 70%),
      radial-gradient(ellipse 35% 40% at 52% 78%, rgba(217,138,30,.8), transparent 72%);
  }
  .front-brand { position: absolute; left: 28px; top: 68px; }
  .front-brand .wordmark {
    font-family: "Josefin Sans", sans-serif; font-weight: 300; font-size: 46px;
    color: var(--white); letter-spacing: 1px; line-height: 1;
  }
  .front-brand .rule { width: 186px; height: 1px; background: var(--rule-gold); margin: 8px 0 6px; }
  .front-brand .tagline {
    font-family: "Josefin Sans", sans-serif; font-weight: 400; font-size: 15px;
    color: var(--white); letter-spacing: .5px;
  }
  .person { position: absolute; left: 30px; top: 192px; }
  .person .name { color: var(--name-orange); font-size: 15px; }
  .person .role { color: var(--title-red); font-size: 14px; margin-top: 6px; }
  .contacts { position: absolute; left: 30px; top: 253px; list-style: none; }
  .contacts li { display: flex; align-items: center; gap: 9px; color: var(--white); font-size: 15px; height: 21px; }
  .contacts svg { width: 13px; height: 13px; flex: none; }

  /* Back */
  .card-back {
    left: 388px; top: 505px; width: 567px; height: 352px;
    background: radial-gradient(ellipse 60% 90% at 52% 50%, var(--back-yellow) 30%, var(--back-orange) 100%);
  }
  .back-flame {
    position: absolute; left: 16px; top: 0; width: 120px; height: 352px;
    background: linear-gradient(180deg, rgba(240,140,20,.7), rgba(243,113,34,.35));
    border-radius: 0 60% 0 80% / 0 40% 0 60%;
  }
  .back-logo { position: absolute; left: 150px; top: 100px; display: flex; align-items: center; gap: 14px; }
  .back-logo .mark { width: 62px; height: 62px; border-radius: 50%; background: var(--brand-ochre); opacity: .85; }
  .back-logo .wordmark {
    font-family: "Josefin Sans", sans-serif; font-weight: 300; font-size: 48px;
    color: var(--brand-wine); line-height: 1;
  }
  .back-logo .rule { width: 216px; height: 1px; background: var(--brand-wine); margin: 6px 0 5px; }
  .back-logo .tagline {
    font-family: "Josefin Sans", sans-serif; font-size: 15px; color: var(--brand-ochre); letter-spacing: .6px;
  }
</style>
</head>
<body>

<section class="card card-front" aria-label="Business card front">
  <div class="front-art" role="img" aria-label="Rising phoenix illustration in deep red and amber flame tones"></div>
  <div class="front-brand">
    <div class="wordmark">VALCORNE</div>
    <div class="rule"></div>
    <div class="tagline">HEALTHCARE MARKETING</div>
  </div>
  <div class="person">
    <div class="name">Marla Tenwick</div>
    <div class="role">CEO</div>
  </div>
  <ul class="contacts">
    <li>
      <svg viewBox="0 0 16 16" aria-hidden="true"><path fill="#f7a21b" d="M2 6c0-2 2-3 6-3s6 1 6 3v1h-3V5.5H5V7H2zM4 8h8l2 6H2z"/></svg>
      638-2974(512)
    </li>
    <li>
      <svg viewBox="0 0 16 16" aria-hidden="true"><rect x="1" y="3" width="14" height="10" fill="#f7a21b"/><path d="M1 3l7 6 7-6" fill="none" stroke="#080606" stroke-width="1.3"/></svg>
      marla@valcorne.com
    </li>
    <li>
      <svg viewBox="0 0 16 16" aria-hidden="true"><circle cx="8" cy="8" r="7" fill="#f7a21b"/><path d="M1 8h14M8 1c-3 3-3 11 0 14M8 1c3 3 3 11 0 14" fill="none" stroke="#080606" stroke-width="1"/></svg>
      valcorne.com
    </li>
  </ul>
</section>

<section class="card card-back" aria-label="Business card back">
  <div class="back-flame" role="img" aria-label="Soft orange flame decoration"></div>
  <div class="back-logo">
    <div class="mark"></div>
    <div>
      <div class="wordmark">VALCORNE</div>
      <div class="rule"></div>
      <div class="tagline">HEALTHCARE MARKETING</div>
    </div>
  </div>
</section>

</body>
</html>
```